HearthMile business card and stationary design

We are looking for a simple yet elegant design for our mortgage company business card and stationary.

The card should include:
Name (Marcus Pell)
Title (CEO)
Phone Number (732-555-0182)
Address (48 Birchwell Court, Suite 314, Hazlet, NJ 07730)
Email (email@hearthmile.example)
"NMLS" i.e. (NMLS 61947)
"Company NMLS" (Company NMLS 274615)

Contact Information for Business Card

See above

```html
<!DOCTYPE html>
<html lang="en">
<head>
<meta charset="utf-8">
<title>HearthMile Business Card</title>
<link rel="stylesheet" href="https://fonts.googleapis.com/css2?family=Montserrat:wght@400;500;600;700&display=swap">
<style>
  :root {
    --backdrop: #1a1b1d;
    --card: #1a2633;
    --card-light: #243444;
    --accent: #2fa8e0;
    --text: #ffffff;
    --text-soft: #e4ebf2;
  }
  * { box-sizing: border-box; margin: 0; padding: 0; }
  html, body {
    width: 1200px; height: 960px; overflow: hidden;
    background: var(--backdrop);
    font-family: "Montserrat", sans-serif;
  }
  .sheet {
    width: 1200px; height: 960px;
    display: flex; flex-direction: column; align-items: center; justify-content: center;
    gap: 44px;
  }
  .card {
    position: relative;
    width: 700px; height: 400px;
    background: linear-gradient(135deg, var(--card-light) 0%, var(--card) 55%);
    border-radius: 4px;
    box-shadow: 0 10px 30px rgba(0,0,0,.5);
    overflow: hidden;
  }
  .brand {
    display: flex; align-items: center; gap: 14px;
    color: var(--text); font-weight: 600; letter-spacing: .5px;
  }
  .brand-mark { background: var(--accent); flex: none; }

  .card-front { display: flex; align-items: center; justify-content: center; }
  .card-front .brand { font-size: 78px; }
  .card-front .brand-mark { width: 26px; height: 26px; }

  .card-back .brand {
    position: absolute; top: 62px; right: 44px; font-size: 44px;
  }
  .card-back .brand-mark { width: 16px; height: 16px; }

  .licensing {
    position: absolute; left: 50px; top: 160px;
    color: var(--text-soft); font-size: 15px; line-height: 28px; font-weight: 500;
  }
  .identity-bar {
    position: absolute; left: 0; top: 236px; width: 14px; height: 54px; background: var(--accent);
  }
  .identity { position: absolute; left: 50px; top: 232px; }
  .identity .name { color: var(--accent); font-weight: 700; font-size: 25px; letter-spacing: .5px; }
  .identity .title { color: var(--text); font-weight: 700; font-size: 19px; margin-top: 2px; }

  .address {
    position: absolute; right: 40px; top: 236px; text-align: left;
    color: var(--text-soft); font-size: 15px; line-height: 24px; font-weight: 500;
  }
  .divider {
    position: absolute; left: 50px; right: 36px; top: 302px; height: 2px; background: var(--accent);
  }
  .contacts {
    position: absolute; left: 50px; top: 316px; list-style: none;
    color: var(--text-soft); font-size: 15px; font-weight: 500;
  }
  .contacts li { display: flex; align-items: center; gap: 12px; height: 24px; }
  .contacts svg { width: 18px; height: 18px; flex: none; }
</style>
</head>
<body>
<main class="sheet">
  <section class="card card-front" aria-label="Card front">
    <div class="brand"><span class="brand-mark"></span>HearthMile</div>
  </section>

  <section class="card card-back" aria-label="Card back">
    <div class="brand"><span class="brand-mark"></span>HearthMile</div>

    <div class="licensing">
      <p>"NMLS" i.e. (NMLS 61947)</p>
      <p>Company NMLS 274615</p>
    </div>

    <div class="identity-bar"></div>
    <div class="identity">
      <p class="name">MARCUS PELL</p>
      <p class="title">CEO</p>
    </div>

    <div class="address">
      <p>48 Birchwell Court, Suite</p>
      <p>314, Fernbrook, NJ 07700</p>
    </div>

    <div class="divider"></div>

    <ul class="contacts">
      <li>
        <svg viewBox="0 0 24 24" aria-hidden="true"><path fill="var(--accent)" d="M6.6 10.8a15.1 15.1 0 0 0 6.6 6.6l2.2-2.2a1 1 0 0 1 1-.25 11.4 11.4 0 0 0 3.6.57 1 1 0 0 1 1 1V20a1 1 0 0 1-1 1A17 17 0 0 1 3 4a1 1 0 0 1 1-1h3.5a1 1 0 0 1 1 1c0 1.25.2 2.45.57 3.570a1 1 0 0 1-.25 1z"/></svg>
        732-555-0182
      </li>
      <li>
        <svg viewBox="0 0 24 24" aria-hidden="true"><rect x="2" y="5" width="20" height="14" rx="1.5" fill="var(--accent)"/><path d="M3 6l9 7 9-7" fill="none" stroke="var(--card)" stroke-width="1.6"/></svg>
        email@hearthmile.example
      </li>
      <li>
        <svg viewBox="0 0 24 24" aria-hidden="true"><circle cx="12" cy="12" r="10" fill="var(--accent)"/><path d="M2 12h20M12 2c3 3 3 17 0 20M12 2c-3 3-3 17 0 20" fill="none" stroke="var(--card)" stroke-width="1.3"/></svg>
        www.hearthmile.example
      </li>
    </ul>
  </section>
</main>
</body>
</html>
```